Workshop PPT Update for AI Transformation Sessions

Our strategic consulting firm runs strategy workshops using slides as workshop exercises. These slides are used to communicate to the participants in advance, run the workshops and produce the final deliverable.

It is time for a design "upgrade". We'd like them to be more engaging, hipper and more interesting. These slides are utilitarian, so clean and usable is good. I have attached the example of what we have today. I have also attached an example of another company's slides that I like.

We can't rip off their design nor can we go away 100% from what we have. But I think it is possible to "update" our look to something closer to their look. Grey colors are fine with some color pop.

Slide styles needed are - 1) Cover Page, 2) Instructions Page, 3) Bullet list 4) Worksheet (place for participants to add content 5) Table, 6) Two column.

```html
<!DOCTYPE html>
<html lang="en">
<head>
<meta charset="utf-8">
<title>Kickoff &amp; Discovery — Workshop Slides</title>
<link href="https://fonts.googleapis.com/css2?family=Montserrat:wght@500;600;700;800&family=Lato:wght@400;700&display=swap" rel="stylesheet">
<style>
  :root {
    --canvas: #8f8f8f;
    --slide: #ffffff;
    --slate: #41424f;
    --ink: #2b2b2f;
    --body: #4a4a50;
    --red: #a33a3a;
    --footer: #262628;
    --pink: #f6e9e9;
    --line: #e4e4e8;
  }
  * { box-sizing: border-box; margin: 0; padding: 0; }
  html, body { width: 1200px; height: 4231px; overflow: hidden; background: var(--canvas); }
  body { position: relative; font-family: "Lato", sans-serif; color: var(--body); }

  .slide { position: absolute; left: 60px; width: 1080px; height: 607px; background: var(--slide); overflow: hidden; }
  .abs { position: absolute; }
  .heading { font-family: "Montserrat", sans-serif; font-weight: 800; color: var(--ink); letter-spacing: 0.3px; }
  .accent-bar { position: absolute; width: 56px; height: 4px; background: var(--red); }
  .brand { font-family: "Montserrat", sans-serif; font-weight: 600; color: var(--red); }

  /* footer */
  .footer { position: absolute; left: 0; bottom: 0; width: 1080px; height: 26px; }
  .footer-bar { position: absolute; left: 0; top: 0; }
  .footer-page { position: absolute; left: 61px; top: 8px; font: 700 9px "Montserrat", sans-serif; color: #fff; }
  .footer-copy { position: absolute; left: 440px; width: 200px; top: 9px; text-align: center; font-size: 7px; color: #ddd; }
  .footer-brand { position: absolute; left: 948px; top: 2px; font-size: 21px; }

  /* cover */
  .cover { background: linear-gradient(135deg, #ffffff 0%, #f4f5f7 55%, #e9ebef 100%); }
  .cover .brand { left: 0; width: 100%; top: 208px; text-align: center; font-size: 50px; }
  .cover-title { left: 0; width: 100%; top: 292px; text-align: center; font-family: "Montserrat", sans-serif; font-weight: 700; font-size: 56px; color: var(--ink); }
  .cover-sub { left: 0; width: 100%; top: 374px; text-align: center; font-size: 19px; color: var(--body); }
  .cover-date { left: 42px; top: 557px; font-size: 19px; color: var(--ink); }
  .cover-web { right: 30px; top: 557px; font-size: 19px; color: var(--ink); }

  /* checklists */
  .check-list { list-style: none; position: absolute; }
  .check-list li { position: relative; padding-left: 30px; font-size: 15px; color: var(--body); height: 36px; }
  .check-list svg { position: absolute; left: 0; top: 1px; }

  .side-panel { position: absolute; left: 0; top: 0; bottom: 0; background: var(--slate); }
  .photo { position: absolute; }

  /* workshop overview */
  .panel-heading { position: absolute; left: 26px; top: 100px; font-size: 30px; line-height: 44px; color: #fff; }
  .panel-label { position: absolute; left: 26px; font-size: 15px; color: #fff; }
  .flow-title { position: absolute; left: 400px; top: 38px; font: 600 22px "Montserrat", sans-serif; color: var(--ink); }
  .step { position: absolute; left: 401px; height: 52px; width: 520px; }
  .step-num { position: absolute; left: 0; top: 0; width: 52px; height: 52px; border-radius: 50%; background: var(--red); color: #fff; font: 600 20px/52px "Montserrat", sans-serif; text-align: center; }
  .step-title { position: absolute; left: 75px; top: 2px; font: 600 16px "Montserrat", sans-serif; color: var(--ink); }
  .step-text { position: absolute; left: 75px; top: 28px; font-size: 14px; color: var(--body); }
  .deliverable { position: absolute; left: 409px; top: 489px; width: 445px; height: 76px; background: var(--pink); border-radius: 6px; padding: 20px 0 0 32px; }
  .deliverable b { display: block; font: 600 14px "Montserrat", sans-serif; color: var(--ink); }
  .deliverable span { display: block; margin-top: 6px; font-size: 11px; color: var(--body); }

  /* plan structure */
  .plan { background: linear-gradient(160deg, #ffffff 0%, #f2f2f4 50%, #ebebee 100%); }
  .plan-table { position: absolute; left: 220px; top: 159px; width: 643px; border-collapse: collapse; background: #fff; box-shadow: 0 4px 14px rgba(0,0,0,0.08); border-radius: 8px; overflow: hidden; font-size: 10px; color: var(--body); }
  .plan-table th { height: 62px; font: 600 10px "Montserrat", sans-serif; color: var(--ink); border-bottom: 1px solid var(--line); border-right: 1px solid var(--line); }
  .plan-table td { height: 62px; text-align: center; border-bottom: 1px solid var(--line); border-right: 1px solid var(--line); line-height: 1.5; }
  .plan-table th:last-child, .plan-table td:last-child { border-right: none; }
  .plan-table tr:last-child td { border-bottom: none; height: 56px; }
  .plan-table td.level { text-align: left; padding-left: 10px; }
  .plan-table td.level em { font-style: normal; margin-left: 14px; display: inline-block; vertical-align: middle; text-align: left; }

  /* principles */
  .principle { position: absolute; left: 401px; width: 600px; }
  .principle-dot { position: absolute; left: 0; top: 0; width: 52px; height: 52px; border-radius: 50%; background: var(--red); }
  .principle-dot svg { position: absolute; left: 14px; top: 15px; }
  .principle-title { position: absolute; left: 75px; top: 2px; font: 600 16px "Montserrat", sans-serif; color: var(--ink); }
  .principle-text { position: absolute; left: 75px; top: 28px; width: 500px; font-size: 13.5px; line-height: 22px; color: var(--body); }
</style>
</head>
<body>

<svg width="0" height="0" style="position:absolute">
  <defs>
    <symbol id="tick-ring" viewBox="0 0 16 16">
      <circle cx="8" cy="8" r="6" fill="none" stroke="#a33a3a" stroke-width="1.3"/>
      <path d="M5 8.2l2.2 2.2L13.5 4" fill="none" stroke="#a33a3a" stroke-width="1.5" stroke-linecap="round" stroke-linejoin="round"/>
    </symbol>
    <symbol id="footer-shape" viewBox="0 0 1080 26">
      <polygon points="0,0 900,0 922,26 0,26" fill="#262628"/>
    </symbol>
  </defs>
</svg>

<!-- Slide 1: Cover -->
<section class="slide cover" style="top:84px">
  <div class="abs brand">NorthPath</div>
  <h1 class="abs cover-title">Kickoff &amp; Discovery</h1>
  <p class="abs cover-sub">Sizing &amp; Scoping AI Transformation</p>
  <p class="abs cover-date">January 2024</p>
  <p class="abs cover-web">www.northpath-advisory.com</p>
</section>

<!-- Slide 2: Getting started -->
<section class="slide" style="top:762px">
  <div class="side-panel" style="width:307px"></div>
  <div class="photo" role="img" aria-label="Photo of two colleagues reviewing work on a laptop in an office" style="left:43px;top:75px;width:407px;height:419px;border:4px solid var(--red);background:linear-gradient(135deg,#3c4450 0%,#5d6470 45%,#22262d 100%)"></div>
  <div class="accent-bar" style="left:524px;top:182px"></div>
  <h2 class="abs heading" style="left:524px;top:194px;font-size:28px">GETTING STARTED</h2>
  <ul class="check-list" style="left:518px;top:262px">
    <li><svg width="16" height="16"><use href="#tick-ring"/></svg>Complete the Engagement Sizing Survey.</li>
    <li><svg width="16" height="16"><use href="#tick-ring"/></svg>Collect relevant inputs.</li>
    <li><svg width="16" height="16"><use href="#tick-ring"/></svg>Determine workshop participants &amp; date.</li>
    <li><svg width="16" height="16"><use href="#tick-ring"/></svg>Send invites, to include pre-work.</li>
  </ul>
  <div class="footer">
    <svg class="footer-bar" width="1080" height="26"><use href="#footer-shape"/></svg>
    <span class="footer-page">PAGE |02</span>
    <span class="footer-copy">©Copyrights 2024 NorthPath &nbsp;|&nbsp; All Rights Reserved</span>
    <span class="brand footer-brand">NorthPath</span>
  </div>
</section>

<!-- Slide 3: Stop -->
<section class="slide" style="top:1448px">
  <svg class="abs" width="1080" height="607" style="left:0;top:0" role="img" aria-label="Photo of colleagues in discussion around a meeting table">
    <defs>
      <linearGradient id="meeting-photo" x1="0" y1="0" x2="1" y2="1">
        <stop offset="0" stop-color="#8a8f96"/>
        <stop offset="0.5" stop-color="#5a6270"/>
        <stop offset="1" stop-color="#2e333b"/>
      </linearGradient>
    </defs>
    <polygon points="456,0 1080,0 1080,607 617,607 600,581" fill="url(#meeting-photo)"/>
    <polygon points="456,0 470,0 614,581 600,581" fill="#2b2d33"/>
  </svg>
  <div class="accent-bar" style="left:71px;top:113px"></div>
  <h2 class="abs heading" style="left:71px;top:124px;font-size:30px">STOP!!</h2>
  <p class="abs" style="left:71px;top:172px;font-size:20px;color:var(--ink)">All process need the following</p>
  <ul class="check-list" style="left:65px;top:249px">
    <li><svg width="16" height="16"><use href="#tick-ring"/></svg>Mission &amp; Vision</li>
    <li><svg width="16" height="16"><use href="#tick-ring"/></svg>Strategic Goals &amp; 2024 OKRs (or priorities)</li>
    <li><svg width="16" height="16"><use href="#tick-ring"/></svg>AI Vision: How will AI enable you to multiply your mission?</li>
    <li><svg width="16" height="16"><use href="#tick-ring"/></svg>AI Guiding Principles</li>
  </ul>
  <div class="footer">
    <svg class="footer-bar" width="1080" height="26"><use href="#footer-shape"/></svg>
    <span class="footer-page">PAGE |03</span>
    <span class="footer-copy">©Copyrights 2024 NorthPath &nbsp;|&nbsp; All Rights Reserved</span>
    <span class="brand footer-brand" style="color:#e7d0d0">NorthPath</span>
  </div>
</section>

<!-- Slide 4: Workshop overview -->
<section class="slide" style="top:2139px">
  <div class="side-panel" style="width:335px"></div>
  <div class="accent-bar" style="left:26px;top:85px"></div>
  <h2 class="heading panel-heading">WORKSHOP<br>OVERVIEW</h2>
  <p class="panel-label" style="top:213px">Participants:</p>
  <p class="panel-label" style="top:261px">Duration:</p>
  <p class="panel-label" style="top:310px">Prep Work:</p>
  <h3 class="flow-title">Workshop Flow</h3>
  <div class="step" style="top:105px"><span class="step-num">1</span><span class="step-title">Focus Areas for Ideation</span><span class="step-text">Complete the Engagement Sizing Survey.</span></div>
  <div class="step" style="top:181px"><span class="step-num">2</span><span class="step-title">Forms of Innovation</span><span class="step-text">Leveraging what's available and creating new</span></div>
  <div class="step" style="top:256px"><span class="step-num">3</span><span class="step-title">Problems We'll Solve</span><span class="step-text">Innovation with a purpose</span></div>
  <div class="step" style="top:332px"><span class="step-num">4</span><span class="step-title">Customer Journey</span><span class="step-text">Shifts to own the customer journey</span></div>
  <div class="step" style="top:407px"><span class="step-num">5</span><span class="step-title">Building an AI Action Plan</span><span class="step-text">Moving forward</span></div>
  <div class="deliverable"><b>Deliverables</b><span>Your Company's AI Product &amp; Service Transformation Playbook</span></div>
  <div class="footer">
    <svg class="footer-bar" width="1080" height="26"><use href="#footer-shape"/></svg>
    <span class="footer-page">PAGE |04</span>
    <span class="footer-copy">©Copyrights 2024 NorthPath &nbsp;|&nbsp; All Rights Reserved</span>
    <span class="brand footer-brand">NorthPath</span>
  </div>
</section>

<!-- Slide 5: Plan structure -->
<section class="slide plan" style="top:2842px">
  <h2 class="abs heading" style="left:71px;top:84px;font-size:30px">PLAN STRUCTURE</h2>
  <table class="plan-table">
    <colgroup><col style="width:102px"><col style="width:220px"><col style="width:151px"><col style="width:170px"></colgroup>
    <tr><th>Level</th><th>Planning Element &amp; Definition</th><th>Accountability/Owner</th><th>Frequency of Modification</th></tr>
    <tr><td class="level">1<em>What<br>(overall)</em></td><td>Strategic Priorities</td><td>N/A</td><td>3+ years</td></tr>
    <tr><td class="level">1.1<em>What<br>(this year)</em></td><td>Goals</td><td>Executive Leadership</td><td>1-3 years</td></tr>
    <tr><td class="level">1.1.1<br><em style="margin-left:38px">How</em></td><td>Key Performance Indicators<br>and/or Initiatives</td><td>Executive Leadership</td><td>1 year<br>(w/ qrtly targets)</td></tr>
    <tr><td class="level">1.1.1.1</td><td>Action Items</td><td></td><td>Quarterly/Monthly</td></tr>
  </table>
  <div class="footer">
    <svg class="footer-bar" width="1080" height="26"><use href="#footer-shape"/></svg>
    <span class="footer-page">PAGE |05</span>
    <span class="footer-copy">©Copyrights 2024 NorthPath &nbsp;|&nbsp; All Rights Reserved</span>
    <span class="brand footer-brand">NorthPath</span>
  </div>
</section>

<!-- Slide 6: AI guiding principles -->
<section class="slide" style="top:3538px">
  <div class="side-panel" style="width:335px"></div>
  <div class="accent-bar" style="left:26px;top:84px"></div>
  <h2 class="heading panel-heading">AI GUIDING<br>PRINCIPLES</h2>
  <p class="panel-label" style="top:212px;line-height:24px">What guides our<br>decision-making and<br>approach?</p>
  <svg class="abs" width="4" height="400" style="left:425px;top:80px"><rect width="2" height="400" fill="#d9d9dd"/></svg>
  <div class="principle" style="top:46px"><span class="principle-dot"><svg width="24" height="22" viewBox="0 0 24 22"><path d="M3 11l6 6L21 4" fill="none" stroke="#fff" stroke-width="3.5" stroke-linecap="round" stroke-linejoin="round"/></svg></span><span class="principle-title">Principle #1</span><p class="principle-text">Complete perspective from Executives, Directors, Managers &amp; Staff. Conduct competitive analysis and customer research (optional).</p></div>
  <div class="principle" style="top:143px"><span class="principle-dot"><svg width="24" height="22" viewBox="0 0 24 22"><path d="M3 11l6 6L21 4" fill="none" stroke="#fff" stroke-width="3.5" stroke-linecap="round" stroke-linejoin="round"/></svg></span><span class="principle-title">Principle #2</span><p class="principle-text">Complete perspective from Executives, Directors, Managers &amp; Staff. Conduct competitive analysis and customer research (optional).</p></div>
  <div class="principle" style="top:238px"><span class="principle-dot"><svg width="24" height="22" viewBox="0 0 24 22"><path d="M3 11l6 6L21 4" fill="none" stroke="#fff" stroke-width="3.5" stroke-linecap="round" stroke-linejoin="round"/></svg></span><span class="principle-title">Principle #3</span><p class="principle-text">Complete perspective from Executives, Directors, Managers &amp; Staff. Conduct competitive analysis and customer research (optional).</p></div>
  <div class="principle" style="top:335px"><span class="principle-dot"><svg width="24" height="22" viewBox="0 0 24 22"><path d="M3 11l6 6L21 4" fill="none" stroke="#fff" stroke-width="3.5" stroke-linecap="round" stroke-linejoin="round"/></svg></span><span class="principle-title">Principle #4</span><p class="principle-text">Complete perspective from Executives, Directors, Managers &amp; Staff. Conduct competitive analysis and customer research (optional).</p></div>
  <div class="principle" style="top:430px"><span class="principle-dot"><svg width="24" height="22" viewBox="0 0 24 22"><path d="M3 11l6 6L21 4" fill="none" stroke="#fff" stroke-width="3.5" stroke-linecap="round" stroke-linejoin="round"/></svg></span><span class="principle-title">Principle #5</span><p class="principle-text">Complete perspective from Executives, Directors, Managers &amp; Staff. Conduct competitive analysis and customer research (optional).</p></div>
  <div class="footer">
    <svg class="footer-bar" width="1080" height="26"><use href="#footer-shape"/></svg>
    <span class="footer-page">PAGE |06</span>
    <span class="footer-copy">©Copyrights 2024 NorthPath &nbsp;|&nbsp; All Rights Reserved</span>
    <span class="brand footer-brand">NorthPath</span>
  </div>
</section>

</body>
</html>
```